Cat-products company needs smart, yet endearing, business card

We need a business card design for a new, but up-and-running, business based in Honolulu, Hawaii. The business is Purrnest Nook Co. Our first product is the most environmentally-friendly cat grass kit ever seen on the planet. Future products, currently in the R&D phase, will include a variety of exciting cat scratchers. We also do consulting work to help apartment-dwellers make their home more cat-friendly and, in the future, plan on doing full, custom installs of structure to create high walkways for cats.

Target Market(s)

Middle-aged, apartment-dwelling, middle-class workers who own 1 or more cats and who dote on them.

Industry/Entity Type

Pet Care

Contact Information for Business Card

A striking, professional, yet warm and friendly design is what we're after.

Font styles to use
Serif
Sans Serif
Other font styles liked:
• Comfortaa

Colors

Designer to choose colors to be used in the design.

Requirements
Must have
• The company logo: (see attachment)
• The company name: Purrnest Nook Co
• The web address: www.purrnestnookco.com
• Email: support@purrnestnookco.com
• Phone: +1 (808) 571 6023
• Update (Fri Jun 30 3017 7:45pm Hawaii Time) I would like, is possible, uploaded picture of the cat grass kit on the back of the card with some text along the lines of: Purrnest Nook Co - Maker Of The Leafiest Feline Sprout Set Yet
Nice to have
• A cat picture, cartoon, real or silhouette that illustrates cats in action and/or relaxing; ie using the apartment space to live, play and relax in and being well-contented.
• Most of the website is done in the font: Comfortaa. It might be nice to continue using this for brand consistency.
Should not have
• Hard-to-read fonts.

```html
<!DOCTYPE html>
<html lang="en">
<head>
<meta charset="utf-8">
<title>Purrnest Nook Co — Business Card</title>
<link rel="stylesheet" href="https://fonts.googleapis.com/css2?family=Comfortaa:wght@400;700&display=swap">
<style>
  :root {
    --backdrop: #e6e4e1;
    --card: #ffffff;
    --amber: #f5a81c;
    --cocoa: #5b3a2f;
    --ink: #2b2b2b;
    --rule: #6b6b6b;
    --art-a: #f4eeee;
    --art-b: #d9d2d2;
  }
  * { box-sizing: border-box; margin: 0; padding: 0; }
  html, body { width: 1200px; height: 1000px; overflow: hidden; }
  body {
    background: var(--backdrop);
    font-family: "Comfortaa", sans-serif;
    color: var(--ink);
    position: relative;
  }
  .card {
    position: absolute;
    left: 250px;
    width: 700px;
    height: 400px;
    background: var(--card);
    box-shadow: 0 10px 28px rgba(0,0,0,0.18);
    overflow: hidden;
  }
  .card--front { top: 60px; }
  .card--back { top: 540px; }

  /* front */
  .cat-artwork {
    position: absolute;
    left: 40px; top: 30px;
    width: 300px; height: 340px;
    border-radius: 50%;
    background: radial-gradient(circle at 50% 60%, var(--art-b), var(--art-a) 70%);
  }
  .brand-mark {
    position: absolute;
    display: flex;
    align-items: center;
    gap: 10px;
  }
  .brand-mark__square {
    width: 30px; height: 30px;
    background: var(--cocoa);
    flex: none;
  }
  .brand-mark__name {
    font-weight: 700;
    color: var(--amber);
    line-height: 1.05;
  }
  .card--front .brand-mark { right: 50px; top: 170px; }
  .card--front .brand-mark__name { font-size: 24px; width: 140px; }

  /* back */
  .card--back .brand-mark { left: 40px; top: 55px; }
  .card--back .brand-mark__square { width: 42px; height: 42px; }
  .card--back .brand-mark__name { font-size: 30px; width: 170px; }

  .holder {
    position: absolute;
    right: 40px; top: 40px;
    text-align: right;
  }
  .holder__name {
    font-size: 28px;
    font-weight: 700;
    color: var(--amber);
    letter-spacing: 0.5px;
  }
  .holder__rule {
    position: absolute;
    right: 110px; top: 80px;
    width: 290px; height: 1px;
    background: var(--rule);
  }
  .holder__role {
    position: absolute;
    right: 40px; top: 78px;
    font-size: 17px;
    color: var(--ink);
  }
  .contacts {
    position: absolute;
    right: 40px; top: 118px;
    list-style: none;
    text-align: right;
    font-size: 16px;
    line-height: 23px;
  }
  .contacts li { display: flex; justify-content: flex-end; align-items: center; gap: 10px; }
  .contacts svg { width: 12px; height: 12px; flex: none; }
  .contacts .web-accent { color: var(--amber); }
  .logo-rule {
    position: absolute;
    left: 30px; top: 205px;
    width: 380px; height: 1px;
    background: var(--rule);
  }
  .address {
    position: absolute;
    left: 45px; top: 250px;
    font-size: 18px;
    line-height: 24px;
    color: var(--ink);
  }
  .swoosh { position: absolute; left: 0; top: 0; width: 700px; height: 400px; }
</style>
</head>
<body>

<section class="card card--front" aria-label="Card front">
  <div class="cat-artwork" role="img" aria-label="Illustration of two black cat silhouettes sitting together, tails curling into a heart shape with two small red hearts"></div>
  <div class="brand-mark">
    <span class="brand-mark__square"></span>
    <span class="brand-mark__name">Purrnest Nook Co</span>
  </div>
</section>

<section class="card card--back" aria-label="Card back">
  <svg class="swoosh" viewBox="0 0 700 400" aria-hidden="true">
    <path d="M0,352 C220,362 430,320 560,225 C610,192 660,180 700,176 L700,188 C660,193 615,205 568,236 C440,330 230,372 0,364 Z" fill="var(--amber)"/>
    <path d="M0,370 C230,380 450,340 580,245 C625,215 665,203 700,200 L700,400 L0,400 Z" fill="var(--cocoa)"/>
    <path d="M0,383 C130,388 250,394 380,400 L0,400 Z" fill="var(--amber)"/>
  </svg>

  <div class="brand-mark">
    <span class="brand-mark__square"></span>
    <span class="brand-mark__name">Purrnest Nook Co</span>
  </div>

  <div class="holder"><p class="holder__name">Lena Okafor</p></div>
  <div class="holder__rule"></div>
  <p class="holder__role">Director</p>

  <ul class="contacts">
    <li>+1 (808) 571 6023
      <svg viewBox="0 0 12 12"><path d="M2,1 L4.5,1 L5,4 L3.6,5 C4.3,6.6 5.4,7.7 7,8.4 L8,7 L11,7.5 L11,10 C6,11 1,6 2,1 Z" fill="var(--amber)"/></svg>
    </li>
    <li>support@purrnestnookco.com
      <svg viewBox="0 0 12 12"><rect x="1" y="3" width="10" height="7" fill="var(--amber)"/><path d="M1,3 L6,7 L11,3" stroke="#fff" fill="none"/></svg>
    </li>
    <li><span>www.<span class="web-accent">purrnestnookco</span>.com</span>
      <svg viewBox="0 0 12 12"><circle cx="6" cy="6" r="5" fill="none" stroke="var(--amber)" stroke-width="1.3"/><path d="M1,6 H11 M6,1 V11" stroke="var(--amber)" stroke-width="1"/></svg>
    </li>
  </ul>

  <div class="logo-rule"></div>
  <p class="address">Your Street Address,<br>Country,1234</p>
</section>

</body>
</html>
```